Automotive component supplier needs a business card design

We need a business card design for our company called Velran Global Components Ltd based in the UK. We are a supplier of interior and exterior components to premium car manufacturers such as Corvel Ashby, Hadley Fenn, Marquist and Tavarelli. We would like to see a modern business card design that uses the colour blue.

Target Market(s)

Premium automotive car manufacturers.

Industry/Entity Type

Automotive

Contact Information for Business Card

Company Name : Velran Global Components Limited
Address: 17 Marlow Yard, Upper Heath, Warwick, CV31 8QL, United Kingdom
Web Address : www.velrancomponents-example.co.uk

Font styles to use
Other font styles liked:
• Helvetica

Colors
3176b5
0255a3
85acd3
cfdeed
cee9f5
85cae6
34a6d7
0692cd
9bcb3c

Requirements
Must have
• Clear company logo and a mixture of blue colours.
Nice to have
• A high quality modern image.
Should not have
• Multiple colours.

```html
<!DOCTYPE html>
<html lang="en">
<head>
<meta charset="utf-8">
<title>Velran Global Components – Business Card</title>
<link href="https://fonts.googleapis.com/css2?family=Arimo:wght@400;700&display=swap" rel="stylesheet">
<style>
  :root {
    --backdrop: #1d1d1d;
    --brand-blue: #0a8ecd;
    --accent-green: #9bcb3c;
    --paper: #ffffff;
    --ink: #4a4a4a;
    --rule: #5a5a5a;
  }
  * { box-sizing: border-box; margin: 0; padding: 0; }
  html, body {
    width: 1200px; height: 987px; overflow: hidden;
    background: var(--backdrop);
    font-family: "Arimo", Helvetica, Arial, sans-serif;
  }
  .card {
    position: absolute;
    width: 615px; height: 352px;
    left: 293px;
  }
  .card--front { top: 130px; background: var(--paper); }
  .card--back { top: 505px; background: var(--brand-blue); }

  /* wordmark */
  .wordmark { position: absolute; font-weight: 700; line-height: 1; }
  .wordmark__name { display: flex; align-items: flex-start; gap: 6px; letter-spacing: 2px; }
  .wordmark__tagline { display: block; letter-spacing: 1px; }
  .card--front .wordmark { right: 35px; top: 40px; color: var(--brand-blue); text-align: right; }
  .card--front .wordmark__name { font-size: 46px; justify-content: flex-end; }
  .card--front .wordmark__tagline { font-size: 13px; margin-top: 6px; }
  .wordmark__mark { width: 11px; height: 11px; background: var(--accent-green); margin-top: 2px; }
  .card--back .wordmark { left: 0; right: 0; top: 128px; color: var(--paper); text-align: center; }
  .card--back .wordmark__name { font-size: 74px; justify-content: center; }
  .card--back .wordmark__tagline { font-size: 19px; margin-top: 8px; letter-spacing: 2px; }

  /* person */
  .person { position: absolute; left: 35px; top: 164px; }
  .person__name { font-size: 21px; font-weight: 700; color: var(--brand-blue); letter-spacing: 0.3px; }
  .person__role { font-size: 14px; color: var(--accent-green); margin-top: 6px; }
  .divider { position: absolute; left: 35px; right: 35px; top: 218px; height: 1px; background: var(--rule); }

  .contact-list { position: absolute; left: 35px; top: 231px; list-style: none; }
  .contact-list li { display: flex; align-items: center; gap: 7px; height: 23.5px; font-size: 15px; color: var(--ink); }
  .contact-list li.contact--email { font-size: 13.5px; }
  .contact-list svg { width: 14px; height: 14px; fill: var(--brand-blue); flex: none; }

  .address { position: absolute; right: 35px; top: 231px; font-style: normal; text-align: right; color: var(--ink); font-size: 14.5px; }
  .address span { display: block; height: 23.5px; line-height: 23.5px; }

  .web-band {
    position: absolute; left: 0; top: 326px; width: 570px; height: 26px;
    background: var(--brand-blue); color: var(--paper);
    font-size: 14px; line-height: 26px; padding-left: 35px;
  }
  .corner-tab {
    position: absolute; left: 575px; top: 326px; width: 40px; height: 26px;
    background: var(--accent-green); border-top-left-radius: 6px;
  }
  .card--back .web-address {
    position: absolute; left: 0; right: 0; top: 292px; text-align: center;
    color: var(--paper); font-size: 15px; letter-spacing: 3.2px;
  }
</style>
</head>
<body>
  <section class="card card--front" aria-label="Business card front">
    <div class="wordmark">
      <span class="wordmark__name">VELRAN<span class="wordmark__mark"></span></span>
      <span class="wordmark__tagline">GLOBAL COMPONENTS</span>
    </div>

    <div class="person">
      <p class="person__name">ALDRIC MAYBURY</p>
      <p class="person__role">CEO/Founder</p>
    </div>
    <div class="divider"></div>

    <ul class="contact-list">
      <li>
        <svg viewBox="0 0 24 24" aria-hidden="true"><path d="M6.6 10.8a15.1 15.1 0 0 0 6.6 6.6l2.2-2.2a1 1 0 0 1 1-.25 11.4 11.4 0 0 0 3.6.57 1 1 0 0 1 1 1V20a1 1 0 0 1-1 1A17 17 0 0 1 3 4a1 1 0 0 1 1-1h3.5a1 1 0 0 1 1 1c0 1.25.2 2.45.57 3.57a1 1 0 0 1-.25 1z"/></svg>
        689 555 0142
      </li>
      <li>
        <svg viewBox="0 0 24 24" aria-hidden="true"><path d="M7 1h10a2 2 0 0 1 2 2v18a2 2 0 0 1-2 2H7a2 2 0 0 1-2-2V3a2 2 0 0 1 2-2zm0 3v14h10V4z"/></svg>
        836 555 0179
      </li>
      <li class="contact--email">
        <svg viewBox="0 0 24 24" aria-hidden="true"><path d="M2 5h20v14H2zm2 2v.5l8 5 8-5V7zm0 2.8V17h16V9.8l-8 5z"/></svg>
        aldric@velrancomponents-example.co.uk
      </li>
    </ul>

    <address class="address">
      <span>17 Marlow Yard, Upper Heath</span>
      <span>Warwick, CV31 8QL</span>
      <span>United Kingdom</span>
    </address>

    <div class="web-band">www.velrancomponents-example.co.uk</div>
    <div class="corner-tab"></div>
  </section>

  <section class="card card--back" aria-label="Business card back">
    <div class="wordmark">
      <span class="wordmark__name">VELRAN</span>
      <span class="wordmark__tagline">GLOBAL COMPONENTS</span>
    </div>
    <p class="web-address">www.velrancomponents-example.co.uk</p>
  </section>
</body>
</html>
```